Business Card Design For Marketing Agnecy LVP

Need business card design for marketing agency.

Doug Fenwick
President, CEO
1-555-302-4196
doug@boldpromoperksgroup.example
www.BoldPromoPerksGroup.example

Back Side:
Boost Sales Using Rewards, Incentives & Giveaways
Get A Free Sample Package

Target Market(s)

B2B

Industry/Entity Type

Marketing

Contact Information for Business Card

Doug Fenwick
President, CEO
1-555-302-4196

Back Side:
Get A Free Sample Package

Please note that my current url is OLD DESIGN. I am working on new design and want the business card to match color themes at least on new site. Here is the demo link for new site so you can see the colors I use, etc.

http://layoutcratehub.example/kq/doug/lvp_final/index.html

Requirements
Must have
• Please note that my current url is OLD DESIGN. I am working on new design and want the business card to match color themes at least on new site. Here is the demo link for new site so you can see the colors I use, etc.

Nice to have

Should not have

```html
<!DOCTYPE html>
<html lang="en">
<head>
<meta charset="utf-8">
<title>LVP Business Card – Front and Back</title>
<link rel="stylesheet" href="https://fonts.googleapis.com/css2?family=Montserrat:wght@500;600;700&family=Arimo:wght@400&display=swap">
<style>
  :root {
    --stage: #3b3c3e;
    --card: #1f2022;
    --card-edge: #2a2b2e;
    --brand-blue: #1f7ad1;
    --text-grey: #b9bbbe;
    --text-white: #f4f5f6;
    --rule: #6d6f73;
  }
  * { margin: 0; padding: 0; box-sizing: border-box; }
  html, body {
    width: 1200px;
    height: 1108px;
    overflow: hidden;
    background: var(--stage);
  }
  .stage {
    width: 1200px;
    height: 1108px;
    display: flex;
    justify-content: center;
    align-items: center;
    gap: 70px;
  }
  .card {
    width: 440px;
    height: 760px;
    background: var(--card);
    border: 1px solid var(--card-edge);
    border-radius: 26px;
    box-shadow: 0 18px 40px rgba(0,0,0,.45);
    display: flex;
    flex-direction: column;
    align-items: center;
    text-align: center;
  }

  /* Front */
  .card--front { padding-top: 120px; }
  .brand {
    color: var(--brand-blue);
    font-family: "Montserrat", sans-serif;
    font-weight: 700;
  }
  .brand__name { display: block; font-size: 118px; line-height: 1; letter-spacing: -2px; }
  .brand-full {
    margin-top: 18px;
    color: var(--brand-blue);
    font-family: "Montserrat", sans-serif;
    font-weight: 700;
    font-size: 19px;
    letter-spacing: 3px;
    border-top: 2px solid var(--brand-blue);
    padding-top: 10px;
  }
  .person { margin-top: 78px; }
  .person__name {
    color: var(--brand-blue);
    font-family: "Montserrat", sans-serif;
    font-weight: 600;
    font-size: 25px;
  }
  .person__title {
    margin-top: 4px;
    color: var(--text-grey);
    font-family: "Arimo", sans-serif;
    font-size: 21px;
  }
  .icon-row {
    margin-top: 22px;
    width: 340px;
    display: flex;
    align-items: center;
    gap: 8px;
  }
  .icon-row__rule { flex: 1; height: 1px; background: var(--rule); }
  .icon-tile {
    width: 30px; height: 30px;
    border-radius: 5px;
    background: var(--brand-blue);
    display: flex; align-items: center; justify-content: center;
  }
  .contact {
    margin-top: 16px;
    color: var(--text-grey);
    font-family: "Arimo", sans-serif;
    font-size: 20px;
    line-height: 1.45;
  }
  .contact__phone { font-size: 21px; }

  /* Back */
  .card--back { justify-content: flex-end; padding-bottom: 120px; }
  .brand--small .brand__name { font-size: 58px; letter-spacing: -1px; }
  .pitch {
    margin-top: 26px;
    color: var(--text-white);
    font-family: "Montserrat", sans-serif;
    font-weight: 600;
    font-size: 21px;
    line-height: 1.35;
    text-transform: uppercase;
  }
  .pitch__rule { width: 320px; height: 1px; background: var(--rule); margin: 22px 0 18px; }
  .pitch__url {
    color: var(--text-white);
    font-family: "Arimo", sans-serif;
    font-size: 20px;
  }
</style>
</head>
<body>
<main class="stage">
  <section class="card card--front" aria-label="Card front">
    <div class="brand">
      <span class="brand__name">LVP</span>
    </div>
    <div class="brand-full">BOLD PROMO PERKS GROUP</div>

    <div class="person">
      <p class="person__name">DOUG FENWICK</p>
      <p class="person__title">President, CEO</p>
    </div>

    <div class="icon-row">
      <span class="icon-row__rule"></span>
      <span class="icon-tile" aria-label="Phone">
        <svg width="18" height="18" viewBox="0 0 24 24"><path fill="#1f2022" d="M6.6 10.8a15 15 0 0 0 6.6 6.6l2.2-2.2a1 1 0 0 1 1-.25 11.4 11.4 0 0 0 3.6.57 1 1 0 0 1 1 1V20a1 1 0 0 1-1 1A17 17 0 0 1 3 4a1 1 0 0 1 1-1h3.5a1 1 0 0 1 1 1c0 1.25.2 2.45.57 3.6a1 1 0 0 1-.25 1z"/></svg>
      </span>
      <span class="icon-tile" aria-label="Email">
        <svg width="18" height="18" viewBox="0 0 24 24"><rect x="3" y="5" width="18" height="14" rx="1.5" fill="#1f2022"/><path d="M3.5 6l8.5 7 8.5-7" stroke="#1f7ad1" stroke-width="1.8" fill="none"/></svg>
      </span>
      <span class="icon-tile" aria-label="Website">
        <svg width="18" height="18" viewBox="0 0 24 24"><circle cx="12" cy="12" r="9" fill="#1f2022"/><path d="M3 12h18M12 3c3 3 3 15 0 18M12 3c-3 3-3 15 0 18" stroke="#1f7ad1" stroke-width="1.4" fill="none"/></svg>
      </span>
      <span class="icon-row__rule"></span>
    </div>

    <div class="contact">
      <p class="contact__phone">1-555-302-4196</p>
      <p>doug@boldpromoperksgroup.example</p>
      <p>www.BoldPromoPerksGroup.example</p>
    </div>
  </section>

  <section class="card card--back" aria-label="Card back">
    <div class="brand brand--small">
      <span class="brand__name">LVP</span>
    </div>
    <div class="pitch">
      <p>Boost sales using rewards</p>
      <p>incentives &amp; giveaways</p>
      <p>Get a free sample package</p>
    </div>
    <div class="pitch__rule"></div>
    <p class="pitch__url">www.BoldPromoPerksGroup.example</p>
  </section>
</main>
</body>
</html>
```